Stationary Set Rebrand for Brennick

We are a Canadian Distribution and Service Company that was established in 1969. Over the past 5 decades we have expanded our business and have warehouses across Canada. We specialize in adhesive tapes, adhesives, films, safety, warehouse, shipping, janitorial and packaging supplies.

We have updated our logo design and would like a new corporate branding identity that includes a new fresh Stationary Set (Business Cards, Letterhead, Letterhead MS Word, Envelope, Presentation Folders, Email Signatures, Notepad Covers, etc.)

Target Market(s)

Industrial Business Sector

Font styles to use
Sans Serif

Colors
0054AA
0677BA
7BADD7
CADEEF
E8F1F8
0094D4
00A9DD
6FCCEA
C7EBF8
E9F6FB
00AB8E
00BBA5
67D7C9
C6EFE9
E9F9F6
EB3D1F
EC4F4E
F09395
F8D3D4
FCEDEE

Requirements
Should not have
• Colors not too light, darker colours preferred

```html
<!DOCTYPE html>
<html lang="en">
<head>
<meta charset="utf-8">
<title>Brennick Business Card</title>
<link href="https://fonts.googleapis.com/css2?family=Michroma&family=Saira:wght@400;500;800&display=swap" rel="stylesheet">
<style>
  :root {
    --page: #e4e4e4;
    --card: #ffffff;
    --ink: #1c1a1b;
    --text: #4a4a4a;
    --muted: #6b6b6b;
    --red: #d7171f;
    --rule: #b5b5b5;
    --back-dark: #121213;
    --back-mid: #2a2a2b;
    --back-light: #3a3a3b;
  }
  * { margin: 0; padding: 0; box-sizing: border-box; }
  html, body { width: 1200px; height: 1200px; overflow: hidden; }
  body {
    background: var(--page);
    position: relative;
    font-family: "Saira", sans-serif;
  }
  .card {
    position: absolute;
    width: 696px;
    height: 398px;
    overflow: hidden;
  }
  .card-front { left: 262px; top: 156px; background: var(--card); }
  .card-back { left: 258px; top: 651px; }

  .brand {
    position: absolute;
    left: 78px;
    top: 160px;
    display: flex;
    align-items: center;
    gap: 10px;
  }
  .brand-name {
    font-family: "Saira", sans-serif;
    font-weight: 800;
    font-size: 54px;
    line-height: 1;
    color: var(--ink);
    letter-spacing: -1px;
  }
  .brand-mark { width: 14px; height: 14px; background: var(--red); }

  .divider {
    position: absolute;
    left: 363px;
    top: 99px;
    width: 2px;
    height: 202px;
    background: linear-gradient(to bottom, transparent, var(--rule) 15%, var(--rule) 85%, transparent);
  }

  .contact { position: absolute; left: 389px; top: 105px; }
  .person-name {
    font-family: "Michroma", sans-serif;
    font-size: 20px;
    line-height: 28px;
    color: var(--red);
    font-weight: 400;
    -webkit-text-stroke: 0.8px var(--red);
  }
  .person-title {
    font-size: 15px;
    line-height: 18px;
    color: var(--muted);
    letter-spacing: 0.5px;
  }
  .address {
    margin-top: 20px;
    font-size: 17px;
    line-height: 21px;
    color: var(--text);
    font-style: normal;
    letter-spacing: 0.6px;
  }
  .lines { margin-top: 13px; list-style: none; }
  .lines li {
    display: flex;
    align-items: center;
    height: 21px;
    font-size: 17px;
    color: var(--text);
    letter-spacing: 0.6px;
  }
  .lines svg { width: 14px; height: 14px; margin-right: 12px; fill: var(--red); flex: none; }

  .band-dark {
    position: absolute; left: 0; bottom: 0;
    width: 100%; height: 16px; background: var(--ink);
  }
  .band-red {
    position: absolute; right: 0; bottom: 0;
    width: 275px; height: 33px; background: var(--red);
    clip-path: polygon(31px 0, 100% 0, 100% 100%, 0 100%);
  }
  .band-gap {
    position: absolute; right: 275px; bottom: 0;
    width: 6px; height: 16px; background: var(--card);
    clip-path: polygon(100% 0, 100% 0, 0 100%, 0 100%);
  }
  .website {
    position: absolute; right: 44px; bottom: 6px;
    font-size: 17px; line-height: 20px;
    color: #ffffff; letter-spacing: 0.6px;
  }

  .back-surface {
    width: 100%; height: 100%;
    background: linear-gradient(90deg, var(--back-dark) 0%, var(--back-mid) 45%, var(--back-light) 100%);
  }
</style>
</head>
<body>
  <section class="card card-front">
    <div class="brand">
      <span class="brand-name">Brennick</span>
      <span class="brand-mark"></span>
    </div>
    <div class="divider"></div>
    <div class="contact">
      <h1 class="person-name">DANIEL MARSH</h1>
      <p class="person-title">President</p>
      <address class="address">4120 Cedarline Road<br>Brampton, Canada 51283</address>
      <ul class="lines">
        <li>
          <svg viewBox="0 0 24 24" aria-hidden="true"><path d="M6.6 10.8a15.1 15.1 0 0 0 6.6 6.6l2.2-2.2a1 1 0 0 1 1-.25 11.4 11.4 0 0 0 3.6.57 1 1 0 0 1 1 1V20a1 1 0 0 1-1 1A17 17 0 0 1 3 4a1 1 0 0 1 1-1h3.5a1 1 0 0 1 1 1c0 1.25.2 2.45.57 3.57a1 1 0 0 1-.25 1z"/></svg>
          555-214-0876
        </li>
        <li>
          <svg viewBox="0 0 24 24" aria-hidden="true"><path d="M7 1h10a2 2 0 0 1 2 2v18a2 2 0 0 1-2 2H7a2 2 0 0 1-2-2V3a2 2 0 0 1 2-2zm0 3v15h10V4zm4 16.2h2v1.3h-2z"/></svg>
          555-309-4412
        </li>
        <li>
          <svg viewBox="0 0 24 24" aria-hidden="true"><path d="M2 5h20v14H2zm2 2v.4l8 5.6 8-5.6V7zm0 2.8V17h16V9.8l-8 5.6z"/></svg>
          info@brennick.com
        </li>
      </ul>
    </div>
    <div class="band-dark"></div>
    <div class="band-red"></div>
    <div class="band-gap"></div>
    <span class="website">www.brennick.com</span>
  </section>

  <section class="card card-back">
    <div class="back-surface" role="img" aria-label="Dark card back with a repeating tonal leaf pattern fading from black to grey"></div>
  </section>
</body>
</html>
```